KR Appraisals website redesign

I would like to refresh my existing website of www.krappraisals-example.com with new graphics, look and feel, as well as updated structure and wording. Content and layout changes have been uploaded to this project Brief.

My existing website has a dark feel. I am now looking for a light and energetic feel. Financial Services is my industry, so the website should be reflect that. I would also like to reflect the concepts of Trust, Service and Expertise.

The website must be serious and upmarket.

Target Market(s)

Corporate board members, CFO's, treasurers and controllers
Auditors, tax advisors, private equity and venture capital asset managers, investors, tax authorities

Industry/Entity Type

Financial Service

Coding

Coded - Design and coding required

Number of Pages Required

5+ page

Font styles to use
Sans Serif
Other font styles liked:
• Designer can choose another modern font

Colors
0355a3
3277b5
85acd3
eaf1f7
f37122
f68d4d
9bcb3c
acd037
cadf82

Requirements
Must have
• Good hi resolution pictures that convey "Finance", "Trust", "Service" or "Expertise".
• An anti-bot (such as Captcha) mechanism in the contact form.
Should not have
• Must not have all content on one rolling screen.

```html
<!DOCTYPE html>
<html lang="en">
<head>
<meta charset="utf-8">
<title>KR Appraisals</title>
<link rel="stylesheet" href="https://fonts.googleapis.com/css2?family=Mulish:wght@300;400;600;700&family=Questrial&family=Poppins:wght@700&family=Montserrat:wght@600;700&display=swap">
<style>
:root{
  --blue:#0355a3;
  --blue-mid:#3277b5;
  --blue-deep:#0a4688;
  --blue-bar:#0b4a8c;
  --orange:#f37122;
  --lime:#9bcb3c;
  --ink:#333b44;
  --muted:#6b7480;
  --pale:#f3f5f9;
  --white:#fff;
}
*{box-sizing:border-box;margin:0;padding:0}
html,body{width:1200px;height:3028px;overflow:hidden}
body{position:relative;font-family:'Mulish',sans-serif;color:var(--ink);background:var(--white)}
.abs{position:absolute}
.center{text-align:center}

/* hero */
.hero{position:absolute;left:0;top:0;width:1200px;height:571px;overflow:hidden}
.hero-photo{position:absolute;inset:0;background:linear-gradient(135deg,#3a3f44 0%,#6d7479 38%,#8a9196 55%,#40464b 100%)}
.hero-shade{position:absolute;inset:0;background:rgba(15,20,25,.35)}
.brand{position:absolute;left:143px;top:11px;height:56px;display:flex;align-items:center;gap:10px;color:var(--white);font-family:'Questrial',sans-serif;font-size:20px;letter-spacing:.5px}
.brand-mark{width:22px;height:22px;border:2px solid currentColor}
.nav{position:absolute;right:144px;top:32px;display:flex;gap:0;font-family:'Mulish',sans-serif;font-size:15px;color:var(--white)}
.nav a{color:inherit;text-decoration:none;padding:8px 12px;margin-left:16px;border:2px solid transparent}
.nav a.active{border-color:var(--orange);color:var(--orange);font-weight:700}
.hero-kicker{position:absolute;top:342px;width:100%;text-align:center;color:var(--white);font-family:'Questrial',sans-serif;font-size:26px;letter-spacing:.5px}
.hero-title{position:absolute;top:370px;width:100%;text-align:center;color:var(--white);font-family:'Poppins',sans-serif;font-weight:700;font-size:52px;line-height:68px}
.hero-sub{position:absolute;top:437px;width:100%;text-align:center;color:var(--white);font-size:19px}
.btn-orange{position:absolute;background:var(--orange);color:var(--white);font-weight:700;font-size:16px;display:flex;align-items:center;justify-content:center;gap:8px}
.hero .btn-orange{left:501px;top:482px;width:197px;height:42px}

/* sections */
.section-title{position:absolute;width:100%;text-align:center;font-family:'Questrial',sans-serif;font-size:38px;color:var(--ink);letter-spacing:.5px}
.about{position:absolute;left:0;top:571px;width:1200px;height:502px;background:var(--white)}
.about .kicker{position:absolute;top:144px;width:100%;text-align:center;color:var(--orange);font-size:16px;font-weight:600}
.about .lead{position:absolute;top:174px;width:100%;text-align:center;font-size:16.5px;font-weight:600;color:#4a525c}
.about .body{position:absolute;left:175px;top:205px;width:850px;text-align:center;font-size:12.5px;line-height:23px;color:var(--muted);font-weight:300}
.about .body p{margin-bottom:8px}
.btn-outline{position:absolute;border:1px solid #888;color:var(--ink);font-size:15px;font-weight:600;display:flex;align-items:center;justify-content:center;gap:8px;background:var(--white)}

.services{position:absolute;left:0;top:1073px;width:1200px;height:738px;background:var(--pale)}
.card{position:absolute;width:286px;height:236px;border:2px solid var(--white);overflow:hidden}
.card-photo{position:absolute;inset:0}
.card-shade{position:absolute;inset:0;background:linear-gradient(to bottom,rgba(0,0,0,0) 55%,rgba(0,0,0,.55))}
.card-label{position:absolute;left:0;right:0;bottom:20px;text-align:center;color:var(--white);font-family:'Montserrat',sans-serif;font-weight:700;font-size:14px;font-variant:small-caps;letter-spacing:.6px;font-size:17px}
.card.hover .card-shade{background:rgba(3,85,163,.72)}
.card.hover .card-label{bottom:auto;top:100px;line-height:20px}
.card.hover svg{position:absolute;left:128px;top:160px}

.news{position:absolute;left:0;top:1811px;width:1200px;height:699px;background:var(--white)}
.feature{position:absolute;left:141px;top:169px;width:522px;height:367px;overflow:hidden}
.feature-photo{position:absolute;inset:0;background:linear-gradient(150deg,#dfe4ea 0%,#b7c3cf 40%,#55606b 75%,#1e2227 100%)}
.feature-shade{position:absolute;inset:0;background:linear-gradient(to bottom,rgba(0,0,0,0) 50%,rgba(0,0,0,.75))}
.feature .date{position:absolute;left:25px;top:277px;color:var(--orange);font-size:13px}
.feature .headline{position:absolute;left:25px;top:296px;width:400px;color:var(--white);font-size:16px;font-weight:700;line-height:25px}
.news-item{position:absolute;left:663px;width:396px;padding:0 60px 0 26px;display:flex;flex-direction:column;justify-content:center}
.news-item .date{font-size:13px;color:var(--muted);margin-bottom:6px}
.news-item .headline{font-size:16px;font-weight:700;line-height:25px;color:#2b323a}
.news-item svg{position:absolute;right:26px;top:50%;margin-top:-5px}
.news-item.active{background:var(--orange)}
.news-item.active .date,.news-item.active .headline{color:var(--white)}

/* footer */
.footer{position:absolute;left:0;top:2510px;width:1200px;height:518px;background:var(--blue)}
.footer-card{position:absolute;left:102px;top:87px;width:369px;height:358px;background:var(--blue-deep)}
.lime-top{position:absolute;left:102px;top:87px;width:363px;height:6px;background:var(--lime)}
.lime-side{position:absolute;left:102px;top:87px;width:6px;height:431px;background:var(--lime)}
.footer-brand{position:absolute;left:143px;top:127px;width:251px;height:104px;border:2px solid var(--white);display:flex;align-items:center;justify-content:center;gap:12px;color:var(--white);font-family:'Questrial',sans-serif;font-size:27px}
.footer-brand .brand-mark{width:26px;height:26px}
.contact-row{position:absolute;left:143px;display:flex;gap:12px;color:var(--white);font-size:13.5px;line-height:23px}
.icon-box{width:25px;height:25px;border:1px solid var(--white);display:flex;align-items:center;justify-content:center;flex:none}
.badge{position:absolute;top:453px;height:26px;border-radius:4px;background:rgba(255,255,255,.35)}
.touch-title{position:absolute;left:564px;top:85px;color:var(--white);font-family:'Questrial',sans-serif;font-size:37px}
.field{position:absolute;height:24px;border-bottom:1px solid rgba(255,255,255,.6);color:var(--white);font-size:11.5px;padding-left:3px}
.captcha{position:absolute;left:562px;top:329px;width:282px;height:71px;border:1px solid var(--white);display:flex;align-items:center;padding-left:21px;gap:12px;color:rgba(255,255,255,.8);font-size:13px}
.captcha .tick{width:18px;height:18px;border:1px solid var(--white);border-radius:2px}
.captcha .seal{position:absolute;right:14px;top:16px;width:26px;height:26px;background:rgba(255,255,255,.75);border-radius:50%}
.footer .btn-orange{left:871px;top:361px;width:142px;height:38px;font-size:14.5px}
.bottom-bar{position:absolute;left:0;top:445px;width:1200px;height:73px;background:var(--blue-bar)}
.bottom-links{position:absolute;right:142px;top:465px;color:var(--white);font-size:13px;display:flex;gap:12px}
.copyright{position:absolute;right:142px;top:492px;color:var(--white);font-size:12px}
</style>
</head>
<body>

<header class="hero">
  <div class="hero-photo" role="img" aria-label="Photo of a presenter showing a chart to colleagues in a bright meeting room"></div>
  <div class="hero-shade"></div>
  <div class="brand"><span class="brand-mark"></span>KR Appraisals</div>
  <nav class="nav">
    <a class="active">HOME</a><a>ABOUT US</a><a>SERVICES</a><a>NEWS &amp; VIEWS</a><a>CONTACT US</a>
  </nav>
  <div class="hero-kicker">TRUST IS PARAMOUNT.</div>
  <h1 class="hero-title">Clients Rely On</h1>
  <div class="hero-sub">KR Appraisals For Confidentiality, Transparency And Independence.</div>
  <div class="btn-orange">CONTACT US TODAY</div>
</header>

<section class="about">
  <h2 class="section-title" style="top:82px">ABOUT US</h2>
  <div class="kicker">TRUST, SERVICE &amp; EXPERTISE</div>
  <div class="lead">Trust is paramount. Clients rely on KR Appraisal Services for confidentiality, transparency and independence.</div>
  <div class="body">
    <p>Service is front and center in KR Appraisal Services' product offerings. KR Appraisal Services considers the needs of all stakeholders and the personal needs of the client team involved.</p>
    <p>KR Appraisal Services offers more than a decade of valuation experience and maintains its commitment to continual professional development.</p>
    <p>KR Appraisals, founded in 2012, is a boutique valuation advisory practice servicing companies throughout Europe and North America. We have offices in Leiden and Amsterdam. Through our affiliate partners, we also have offices in New York and London offering transfer pricing, derivatives modelling, and machinery &amp; equipment valuation.</p>
  </div>
  <div class="btn-outline" style="left:529px;top:378px;width:142px;height:38px">READ MORE
    <svg width="15" height="15" viewBox="0 0 16 16"><circle cx="8" cy="8" r="7" fill="none" stroke="#333b44" stroke-width="1.4"/><path d="M5 8h6M8.5 5.5 11 8l-2.5 2.5" fill="none" stroke="#333b44" stroke-width="1.4"/></svg>
  </div>
</section>

<section class="services">
  <h2 class="section-title" style="top:80px">OUR SERVICES</h2>
  <div class="card" style="left:143px;top:153px">
    <div class="card-photo" role="img" aria-label="Photo of hands reviewing charts on a tablet" style="background:linear-gradient(150deg,#c9d2dc,#6f7c8a 60%,#2c333b)"></div>
    <div class="card-shade"></div><div class="card-label">Business Valuation</div>
  </div>
  <div class="card hover" style="left:457px;top:153px">
    <div class="card-photo" role="img" aria-label="Photo of a laptop on a desk showing property data" style="background:linear-gradient(150deg,#7f9fc0,#3f6690)"></div>
    <div class="card-shade"></div><div class="card-label">Intellectual Property<br>Valuation</div>
    <svg width="28" height="28" viewBox="0 0 28 28"><circle cx="14" cy="14" r="12.5" fill="none" stroke="#fff" stroke-width="1.6"/><path d="M14 8v12M8 14h12" stroke="#fff" stroke-width="1.6"/></svg>
  </div>
  <div class="card" style="left:771px;top:153px">
    <div class="card-photo" role="img" aria-label="Photo of a business team meeting in a loft office" style="background:linear-gradient(150deg,#a58c74,#d9d4cc 45%,#5e6670)"></div>
    <div class="card-shade"></div><div class="card-label">M &amp; A Advisory</div>
  </div>
  <div class="card" style="left:300px;top:416px">
    <div class="card-photo" role="img" aria-label="Photo of a team planning around a whiteboard in warm light" style="background:linear-gradient(150deg,#e8d9b8,#a8926e 50%,#3b3a36)"></div>
    <div class="card-shade"></div><div class="card-label">Business Plan Coaching</div>
  </div>
  <div class="card" style="left:614px;top:416px">
    <div class="card-photo" role="img" aria-label="Photo of a hand signing a financial document" style="background:linear-gradient(150deg,#eef0f2,#9aa3ad 55%,#3a4048)"></div>
    <div class="card-shade"></div><div class="card-label">Purchase Price Allocation</div>
  </div>
</section>

<section class="news">
  <h2 class="section-title" style="top:82px">NEWS &amp; VIEWS</h2>
  <div class="feature">
    <div class="feature-photo" role="img" aria-label="Photo of colleagues analysing charts on a tablet and paper reports"></div>
    <div class="feature-shade"></div>
    <div class="date">March 9, 2016</div>
    <div class="headline">Dutch GAAP Update – Goodwill and Definitions of Value</div>
  </div>
  <div class="news-item" style="top:169px;height:116px">
    <div class="date">February 4, 2016</div>
    <div class="headline">Martin Vos to Speak at Bridge2Markets on Feb 18 in Oosterhout, the Netherlands</div>
    <svg width="14" height="10" viewBox="0 0 14 10"><path d="M0 5h12M8 1l4 4-4 4" fill="none" stroke="#0355a3" stroke-width="1.5"/></svg>
  </div>
  <div class="news-item active" style="top:285px;height:114px">
    <div class="date">February 4, 2016</div>
    <div class="headline">KR Appraisals presenteert bij Bridge2Markets op 18 februari in Oosterhout</div>
    <svg width="14" height="10" viewBox="0 0 14 10"><path d="M0 5h12M8 1l4 4-4 4" fill="none" stroke="#fff" stroke-width="1.5"/></svg>
  </div>
  <div class="news-item" style="top:399px;height:137px">
    <div class="date">September 7, 2015</div>
    <div class="headline">Amstel Business School Extends Financial Training Contract with KR Appraisals</div>
    <svg width="14" height="10" viewBox="0 0 14 10"><path d="M0 5h12M8 1l4 4-4 4" fill="none" stroke="#0355a3" stroke-width="1.5"/></svg>
  </div>
  <div class="btn-outline" style="left:536px;top:575px;width:127px;height:38px">VIEW ALL
    <svg width="15" height="15" viewBox="0 0 16 16"><circle cx="8" cy="8" r="7" fill="none" stroke="#333b44" stroke-width="1.4"/><path d="M5 8h6M8.5 5.5 11 8l-2.5 2.5" fill="none" stroke="#333b44" stroke-width="1.4"/></svg>
  </div>
</section>

<footer class="footer">
  <div class="bottom-bar"></div>
  <div class="footer-card"></div>
  <div class="lime-top"></div>
  <div class="lime-side"></div>
  <div class="footer-brand"><span class="brand-mark"></span>KR Appraisals</div>
  <div class="contact-row" style="top:264px">
    <span class="icon-box"><svg width="11" height="14" viewBox="0 0 11 14"><path d="M5.5 13S1 8 1 5a4.5 4.5 0 0 1 9 0c0 3-4.5 8-4.5 8z" fill="none" stroke="#fff" stroke-width="1.3"/><circle cx="5.5" cy="5" r="1.5" fill="#fff"/></svg></span>
    <span>Lindenlaan 48,<br>2311 KB Leiden,<br>The Netherlands</span>
  </div>
  <div class="contact-row" style="top:350px">
    <span class="icon-box"><svg width="13" height="13" viewBox="0 0 13 13"><path d="M3 1l2 3-1.3 1.3a7 7 0 0 0 4 4L9 8l3 2-1.5 2C5.5 12 1 7.5 1 2.5z" fill="#fff"/></svg></span>
    <span style="line-height:25px">+31 70 555 0142</span>
  </div>
  <div class="contact-row" style="top:393px">
    <span class="icon-box"><svg width="13" height="11" viewBox="0 0 13 11"><rect x="1" y="1" width="11" height="9" fill="none" stroke="#fff" stroke-width="1.2"/><path d="M1 1l5.5 5L12 1" fill="none" stroke="#fff" stroke-width="1.2"/></svg></span>
    <span style="line-height:25px">info@krappraisals-example.com</span>
  </div>
  <div class="badge" style="left:143px;width:134px"></div>
  <div class="badge" style="left:300px;width:98px"></div>

  <h2 class="touch-title">GET IN TOUCH</h2>
  <div class="field" style="left:561px;top:159px;width:221px">Name*</div>
  <div class="field" style="left:808px;top:159px;width:222px">Email*</div>
  <div class="field" style="left:561px;top:207px;width:221px">Phone*</div>
  <div class="field" style="left:808px;top:207px;width:222px">Company*</div>
  <div class="field" style="left:561px;top:256px;width:469px;height:40px">Message*</div>
  <div class="captcha"><span class="tick"></span>I'm not a Robot<span class="seal"></span></div>
  <div class="btn-orange">READ MORE
    <svg width="15" height="15" viewBox="0 0 16 16"><circle cx="8" cy="8" r="7" fill="none" stroke="#fff" stroke-width="1.4"/><path d="M5 8h6M8.5 5.5 11 8l-2.5 2.5" fill="none" stroke="#fff" stroke-width="1.4"/></svg>
  </div>
  <div class="bottom-links"><span>Home</span><span>|</span><span>About Us</span><span>|</span><span>Services</span><span>|</span><span>News &amp; Views</span><span>|</span><span>Contact Us</span></div>
  <div class="copyright">Copyright © 2019 KR Appraisals. All Rights Reserved.</div>
</footer>

</body>
</html>
```